use my brand and make an elegant business card  with it

Target Market(s)
male and female ' ages 25 to 45 age- who appreciate the highest quality goods, experiences, services, brands and relationships
Industry/Entity Type
Business
Requirements
Must have
- my logo integrated into the design-note the uploaded file
front: just logo and the phrase: Pure. Craft. Fine. Grace
back informations:
Maren Tosvik
Director
phone: +1 604 2957318
www.matosvik.com
email: marentosvik@matosvik.com
the pin of Facebook (F) and tweeter (T)
Nice to have
- contrast of the colors black gold and silver
Should not have
- cartoons or whimsical design

```html
<!DOCTYPE html>
<html lang="en">
<head>
<meta charset="utf-8">
<title>Ma Tosvik — Business Card</title>
<link rel="stylesheet" href="https://fonts.googleapis.com/css2?family=Michroma&display=swap">
<style>
  :root {
    --backdrop: #2a2622;
    --card-black: #121212;
    --card-black-soft: #1c1c1c;
    --gold: #d4b21c;
    --gold-deep: #a8870f;
    --silver: #c9c9c9;
    --text-font: "Michroma", sans-serif;
  }
  * { margin: 0; padding: 0; box-sizing: border-box; }
  html, body {
    width: 1200px;
    height: 960px;
    overflow: hidden;
    background: var(--backdrop);
  }
  .canvas {
    position: relative;
    width: 1200px;
    height: 960px;
    display: flex;
    flex-direction: column;
    align-items: center;
    justify-content: center;
    gap: 60px;
  }
  .card {
    position: relative;
    width: 620px;
    height: 354px;
    background: radial-gradient(ellipse at 50% 45%, var(--card-black-soft), var(--card-black) 75%);
    box-shadow: 0 10px 30px rgba(0,0,0,.45);
    font-family: var(--text-font);
  }
  .corner-ornament {
    position: absolute;
    width: 46px;
    height: 30px;
    background: linear-gradient(135deg, var(--gold), var(--gold-deep));
    opacity: .85;
  }
  .corner-ornament.top-left { top: 22px; left: 22px; }
  .corner-ornament.top-right { top: 22px; right: 22px; }
  .corner-ornament.bottom-left { bottom: 22px; left: 22px; }
  .corner-ornament.bottom-right { bottom: 22px; right: 22px; }

  /* Front */
  .card-front .brand-block {
    position: absolute;
    left: 150px;
    top: 118px;
  }
  .brand-name {
    color: var(--gold);
    font-size: 42px;
    line-height: 1;
    letter-spacing: 2px;
    display: flex;
    align-items: center;
    gap: 14px;
  }
  .brand-mark {
    width: 18px;
    height: 18px;
    border-radius: 50%;
    background: var(--gold);
  }
  .tagline {
    margin-top: 20px;
    color: var(--silver);
    font-size: 15px;
    letter-spacing: 3px;
  }

  /* Back */
  .card-back .contact-block {
    position: absolute;
    left: 110px;
    top: 62px;
    color: var(--gold);
  }
  .holder-line {
    font-size: 21px;
    letter-spacing: 2px;
    margin-bottom: 20px;
  }
  .contact-line {
    font-size: 13px;
    letter-spacing: 2px;
    line-height: 2;
  }
  .social-pin {
    position: absolute;
    width: 14px;
    height: 14px;
    background: var(--gold);
  }
  .social-pin.left { left: 78px; top: 170px; }
  .social-pin.right { right: 78px; top: 250px; }
</style>
</head>
<body>
<main class="canvas">
  <section class="card card-front" aria-label="Card front">
    <div class="corner-ornament top-left" role="img" aria-label="Gold filigree corner ornament"></div>
    <div class="corner-ornament top-right" role="img" aria-label="Gold filigree corner ornament"></div>
    <div class="corner-ornament bottom-left" role="img" aria-label="Gold filigree corner ornament"></div>
    <div class="corner-ornament bottom-right" role="img" aria-label="Gold filigree corner ornament"></div>
    <div class="brand-block">
      <div class="brand-name"><span>MA TOSVIK</span><span class="brand-mark"></span></div>
      <p class="tagline">Pure. Craft. Fine. Grace</p>
    </div>
  </section>

  <section class="card card-back" aria-label="Card back">
    <div class="corner-ornament top-left" role="img" aria-label="Gold filigree corner ornament"></div>
    <div class="corner-ornament top-right" role="img" aria-label="Gold filigree corner ornament"></div>
    <div class="corner-ornament bottom-left" role="img" aria-label="Gold filigree corner ornament"></div>
    <div class="corner-ornament bottom-right" role="img" aria-label="Gold filigree corner ornament"></div>
    <span class="social-pin left" aria-label="Social profile"></span>
    <span class="social-pin right" aria-label="Social profile"></span>
    <div class="contact-block">
      <p class="holder-line">Maren Tosvik - Director</p>
      <p class="contact-line">phone: +1 604 2957318</p>
      <p class="contact-line">www.matosvik.com</p>
      <p class="contact-line">email: marentosvik@matosvik.com</p>
    </div>
  </section>
</main>
</body>
</html>
```